TernVAX Business Cards

Create business cards for our exciting new software company. We provide cloud billing systems and provisioning software for campany that need monthly SaaS and Cloud Billing

Target Market(s)

Enterprise businesses, b2b, telecom carriers, software manufactures

Industry/Entity Type

Software

```html
<!DOCTYPE html>
<html lang="en">
<head>
<meta charset="utf-8">
<title>TernVAX Business Cards</title>
<link rel="stylesheet" href="https://fonts.googleapis.com/css2?family=Jost:wght@400;500&display=swap">
<style>
  :root {
    --backdrop: #3b3b3d;
    --navy: #1d3a5a;
    --steel: #4b7b9d;
    --paper: #f0f0f0;
    --sky: #7cc3e0;
    --ink: #24344a;
    --muted: #9aa3ad;
  }
  * { margin: 0; padding: 0; box-sizing: border-box; }
  html, body { width: 1200px; height: 900px; overflow: hidden; background: var(--backdrop); }
  body { position: relative; font-family: "Jost", "Helvetica Neue", Arial, sans-serif; }
  .card-shapes { position: absolute; inset: 0; }
  .text { position: absolute; white-space: nowrap; }

  .front-name { left: 108px; top: 484px; font-size: 32px; font-weight: 500; color: var(--sky); letter-spacing: 0.5px; }
  .front-tagline { left: 190px; top: 524px; width: 100px; text-align: right; font-size: 6px; line-height: 8px; color: var(--sky); letter-spacing: 0.4px; }
  .front-url { left: 108px; top: 550px; font-size: 9px; color: var(--sky); letter-spacing: 6.4px; }

  .back-block { position: absolute; right: 108px; top: 440px; text-align: right; color: var(--ink); }
  .back-name { font-size: 27px; font-weight: 500; color: var(--sky); line-height: 30px; }
  .back-tagline { font-size: 6px; line-height: 8px; letter-spacing: 0.4px; margin-top: 4px; }
  .person { font-size: 15px; font-weight: 500; letter-spacing: 1px; margin-top: 20px; line-height: 16px; }
  .role { font-size: 11px; font-weight: 500; letter-spacing: 1px; line-height: 13px; }
  .contact { font-size: 12px; font-weight: 500; letter-spacing: 0.8px; line-height: 14px; }
  .contact-first { margin-top: 6px; }
  .label { color: var(--muted); }
</style>
</head>
<body>
  <svg class="card-shapes" width="1200" height="900" viewBox="0 0 1200 900" aria-hidden="true">
    <defs>
      <linearGradient id="band-front" x1="0" y1="0" x2="1" y2="1">
        <stop offset="0" stop-color="#5587aa"/>
        <stop offset="1" stop-color="#1d3a5a"/>
      </linearGradient>
      <linearGradient id="band-back" x1="1" y1="0" x2="0" y2="1">
        <stop offset="0" stop-color="#5587aa"/>
        <stop offset="1" stop-color="#1d3a5a"/>
      </linearGradient>
    </defs>
    <g class="card-front">
      <path fill="url(#band-front)" d="M58 300 H305 C455 300 583 420 583 535 Q583 575 552 600 H58 Z"/>
      <path fill="var(--navy)" d="M58 300 H300 C440 325 556 430 556 535 Q556 575 535 600 H58 Z"/>
    </g>
    <g class="card-back">
      <path fill="url(#band-back)" d="M895 300 H1142 V600 H655 C628 565 618 530 618 495 C618 385 750 300 895 300 Z"/>
      <path fill="var(--paper)" d="M895 300 H1142 V600 H683 C655 565 645 530 645 495 C645 400 765 328 880 316 Z"/>
    </g>
  </svg>

  <div class="text front-name">TernVAX</div>
  <div class="text front-tagline">CLOUD BILLING AND<br>OPERATIONAL SUPPORT SYSTEMS</div>
  <div class="text front-url">WWW.TERNVAX.COM</div>

  <div class="back-block">
    <div class="back-name">TernVAX</div>
    <div class="back-tagline">CLOUD BILLING AND<br>OPERATIONAL SUPPORT SYSTEMS</div>
    <div class="person">DANA WHITFIELD</div>
    <div class="role">MANAGER</div>
    <div class="contact contact-first"><span class="label">P:</span> 555-014-2290 <span class="label">F:</span> 555-014-7731</div>
    <div class="contact"><span class="label">E:</span> INFO@TERNVAX.COM <span class="label">W:</span> WWW.TERNVAX.COM</div>
  </div>
</body>
</html>
```